Brellwick Partners, LLC Stationary

Brellwick Partners, LLC is a new financial planning and consulting company. We are looking for designs on business cards, letterhead, envelopes, and anything else that would be useful. Our preference for business card design is two sided. We are looking for a professional and clean look with incorporating the logo and patriotic feel. Thank you to all who participate and good luck!

```html
<!DOCTYPE html>
<html lang="en">
<head>
<meta charset="utf-8">
<title>Brellwick Partners, LLC Stationery</title>
<link href="https://fonts.googleapis.com/css2?family=Michroma&family=Didact+Gothic&display=swap" rel="stylesheet">
<style>
  :root {
    --backdrop: #e9e9e9;
    --paper: #f4f4f4;
    --navy: #1f4468;
    --flap-navy: #0e355c;
    --red: #b5262f;
    --ink: #555a60;
    --faint: rgba(31, 68, 104, 0.06);
  }
  * { margin: 0; padding: 0; box-sizing: border-box; }
  html, body { width: 1200px; height: 821px; overflow: hidden; }
  body {
    position: relative;
    background: var(--backdrop);
    font-family: "Didact Gothic", sans-serif;
  }
  .sheet { position: absolute; background: var(--paper); overflow: hidden; }
  .wave { position: absolute; left: 0; bottom: 0; width: 100%; }
  .brand-name {
    font-family: "Michroma", sans-serif;
    color: var(--navy);
    font-weight: 400;
    white-space: nowrap;
    letter-spacing: 0.02em;
  }
  .brand-dot {
    display: inline-block;
    border-radius: 50%;
    background: var(--red);
    vertical-align: middle;
  }
  .faint-disc {
    position: absolute;
    border-radius: 50%;
    background: var(--faint);
  }

  /* Letterhead */
  .letterhead { left: 69px; top: 110px; width: 468px; height: 662px; }
  .letterhead .brand {
    position: absolute; top: 50px; left: 0; width: 100%;
    display: flex; justify-content: center; align-items: center; gap: 8px;
  }
  .letterhead .brand-name { font-size: 15px; }
  .letterhead .brand-dot { width: 14px; height: 14px; }
  .letterhead .faint-disc { left: 90px; top: 260px; width: 280px; height: 280px; }
  .letterhead .footer {
    position: absolute; left: 0; bottom: 6px; width: 100%;
    color: #fff; text-align: center; font-size: 7.5px; line-height: 13px;
  }
  .footer .contact-row { display: flex; justify-content: center; gap: 9px; }
  .contact-row span { display: inline-flex; align-items: center; gap: 3px; }
  .contact-row svg { width: 7px; height: 7px; }

  /* Envelope front */
  .envelope-front { left: 613px; top: 224px; width: 523px; height: 249px; }
  .envelope-front .brand {
    position: absolute; left: 22px; top: 34px;
    display: flex; align-items: center; gap: 7px;
  }
  .envelope-front .brand-name { font-size: 12px; }
  .envelope-front .brand-dot { width: 11px; height: 11px; }
  .envelope-front .return-address {
    position: absolute; left: 22px; top: 66px;
    font-size: 7.5px; line-height: 10px; color: var(--ink);
  }
  .envelope-front .faint-disc { left: 300px; top: 20px; width: 200px; height: 200px; }

  /* Envelope back */
  .envelope-back { left: 618px; top: 514px; width: 524px; height: 248px; }
  .envelope-back .flap {
    position: absolute; left: 12px; top: 0; width: 500px; height: 88px;
    background: var(--flap-navy);
    border-radius: 0 0 12px 12px;
    display: flex; justify-content: center; align-items: center;
  }
  .flap .brand-name { color: #fff; font-size: 10px; }
</style>
</head>
<body>

  <section class="sheet letterhead" aria-label="Letterhead">
    <div class="brand">
      <span class="brand-dot"></span>
      <span class="brand-name">BRELLWICK PARTNERS, LLC</span>
    </div>
    <div class="faint-disc"></div>
    <svg class="wave" viewBox="0 0 468 110" preserveAspectRatio="none" height="110">
      <path d="M0,0 C70,40 170,66 280,72 C170,70 70,54 0,30 Z" fill="var(--red)"/>
      <path d="M0,30 C90,58 180,70 270,73 C350,74 420,62 468,32 L468,110 L0,110 Z" fill="var(--navy)"/>
    </svg>
    <div class="footer">
      <div>4120 Larkspur Way, Fairbanks, Alaska 99701</div>
      <div class="contact-row">
        <span><svg viewBox="0 0 10 10"><path d="M2,0 L4,3 L3,4 C4,6 5,7 6,7 L7,6 L10,8 L8,10 C4,10 0,6 0,2 Z" fill="#fff"/></svg>555 210 4418</span>
        <span><svg viewBox="0 0 10 10"><rect x="2" y="0" width="6" height="3" fill="#fff"/><rect x="0" y="4" width="10" height="4" fill="#fff"/><rect x="2" y="8" width="6" height="2" fill="#fff"/></svg>555 210 4419</span>
        <span><svg viewBox="0 0 10 10"><rect x="0" y="2" width="10" height="7" fill="#fff"/><path d="M0,2 L5,6 L10,2" stroke="var(--navy)" fill="none"/></svg>hello@brellwick.com</span>
        <span><svg viewBox="0 0 10 10"><circle cx="5" cy="5" r="4.5" fill="none" stroke="#fff"/><path d="M0.5,5 H9.5 M5,0.5 C2,3 2,7 5,9.5 C8,7 8,3 5,0.5" stroke="#fff" fill="none" stroke-width="0.8"/></svg>www.brellwick.com</span>
      </div>
    </div>
  </section>

  <section class="sheet envelope-front" aria-label="Envelope front">
    <div class="brand">
      <span class="brand-dot"></span>
      <span class="brand-name">BRELLWICK PARTNERS, LLC</span>
    </div>
    <div class="return-address">4120 Larkspur Way<br>Fairbanks, Alaska 99701</div>
    <div class="faint-disc"></div>
    <svg class="wave" viewBox="0 0 523 65" preserveAspectRatio="none" height="65">
      <path d="M0,0 C70,28 170,48 320,56 C180,56 70,40 0,18 Z" fill="var(--red)"/>
      <path d="M0,20 C100,46 210,57 310,57 C400,57 470,46 523,32 L523,65 L0,65 Z" fill="var(--navy)"/>
    </svg>
  </section>

  <section class="sheet envelope-back" aria-label="Envelope back">
    <div class="flap">
      <span class="brand-name">BRELLWICK PARTNERS, LLC</span>
    </div>
  </section>

</body>
</html>
```